Summit Bodyform Gym Website

We need a website design for our gym.

Summit is the UAE's first calisthenics and parkour gym. The theme under which the gym revolves is that one does not require any machinery to workout as our bodies could be themselves the machinery. The gym is designed to be the more of a social hub rather than an "in-and-out" gym, where people come train, have fun, hang out and socialize for a few hours rather than just train for 60 minutes then leave. The gym is designed to be a big open space with lots of natural sunlight, natural wood and plants all over the place to create a natural and refreshing setting. We also use recycled material throughout the gym and recycle our waste as being green is part of our philosophy. We currently also have some of the world's top and most recognized calisthenics athletes working with us.

We would like our website to reflect all that as well as provide a simple, interactive and fun way for visitors to be able to get class and gym information, check out gym media and contact us for bookings.

Target Market(s)

Ages 15-35

Industry/Entity Type

Fitness

Coding

Coded - Design and coding required

Number of Pages Required

4 page

Font styles to use
Decorative

Colors
0792cd

Requirements
Must have
• Class descriptions
• Gym description
• Class schedules
• Trainer profiles
• Gym philosophy
• Contact Details
Nice to have
• A link to contact us directly for a free first trial class

```html
<!DOCTYPE html>
<html lang="en">
<head>
<meta charset="utf-8">
<title>Summit Bodyform Gym</title>
<link rel="stylesheet" href="https://fonts.googleapis.com/css2?family=Open+Sans:wght@400;600;700&display=swap">
<style>
:root{
  --brand:#0792cd;
  --brand-dark:#0a7fae;
  --brand-light:#39b4dc;
  --ink:#333;
  --muted:#8a8a8a;
  --line:#cfd8dc;
  --dark:#1c1c1c;
  --white:#fff;
}
*{box-sizing:border-box;margin:0;padding:0}
html,body{width:1200px;height:3383px;overflow:hidden}
body{font-family:"Open Sans",Arial,sans-serif;color:var(--ink);background:var(--white);position:relative}
section,header,nav,footer{position:absolute;left:0;width:1200px}
.abs{position:absolute}
.center{text-align:center;left:0;width:1200px}

/* header */
.site-header{top:0;height:99px;background:var(--white)}
.brand{left:100px;top:18px;display:flex;align-items:center;gap:12px}
.brand-dot{width:36px;height:36px;border-radius:50%;background:var(--brand)}
.brand-name{font-size:26px;font-weight:700;color:#1b2a38}
.contact-chip{top:22px;display:flex;align-items:center;gap:16px;font-size:15px;color:#555}
.contact-chip .ring{width:46px;height:46px;border:2px solid var(--brand);border-radius:50%;display:flex;align-items:center;justify-content:center}

/* nav */
.main-nav{top:99px;height:72px;background:linear-gradient(180deg,#2aa9d6,#0d8fc4)}
.main-nav a{position:absolute;top:25px;color:var(--white);font-size:14px;font-weight:600;text-decoration:none}

/* hero */
.hero{top:171px;height:533px}
.hero-photo{position:absolute;inset:0;background:linear-gradient(135deg,#3b3a36,#6b5e4c 40%,#2f3a3d 75%,#1e2527)}
.hero-title{top:210px;font-size:42px;line-height:62px;color:var(--white);font-weight:400;text-shadow:0 2px 6px rgba(0,0,0,.5)}
.slider-arrow{left:34px;top:260px;width:46px;height:46px;border:2px solid rgba(255,255,255,.6);border-radius:50%;display:flex;align-items:center;justify-content:center}

/* welcome */
.welcome{top:704px;height:347px;background:linear-gradient(180deg,#1b9ec9,#118dbd 60%,#2aa5d0)}
.welcome h2{top:62px;font-size:26px;font-weight:600;color:var(--white);letter-spacing:.5px}
.welcome p{left:230px;width:740px;top:126px;font-size:12px;line-height:20px;color:#e6f5fb;text-align:center}
.btn{position:absolute;display:flex;align-items:center;justify-content:center;font-size:14px;font-weight:600;text-decoration:none}
.btn-outline-light{left:521px;top:223px;width:158px;height:52px;border:2px solid rgba(255,255,255,.8);color:var(--white)}

/* services */
.services{top:1051px;height:515px}
.section-title{font-size:26px;font-weight:600}
.services .section-title{top:64px;color:var(--brand)}
.service-card{top:179px;width:240px;height:268px;border:2px solid #dfe5e8;text-align:center;background:var(--white)}
.service-card.active{border-color:var(--brand)}
.service-icon{position:absolute;left:75px;top:-45px;width:90px;height:90px;border-radius:50%;background:var(--white);border:2px solid #dfe5e8;display:flex;align-items:center;justify-content:center}
.service-card.active .service-icon{background:var(--brand);border-color:var(--brand)}
.service-card h3{margin-top:70px;font-size:16px;font-weight:600;color:#333}
.service-card p{margin:14px 20px 0;font-size:12px;line-height:17px;color:var(--muted)}
.service-card .btn{left:52px;top:186px;width:135px;height:43px;border:2px solid var(--brand);color:var(--brand)}
.service-card.active .btn{background:var(--brand);color:var(--white)}

/* gym description */
.gym-description{top:1566px;height:458px;background:linear-gradient(135deg,#2a2624,#3b322c 50%,#1f1d1c)}
.gym-description h2{left:99px;top:64px;font-size:26px;font-weight:600;color:var(--white)}
.gym-description p{left:99px;width:515px;font-size:12px;line-height:19px;color:#d8d8d8}
.gym-description .btn{left:99px;top:340px;width:131px;height:40px;background:var(--brand);color:var(--white)}
.video-frame{left:636px;top:81px;width:465px;height:289px;border:4px solid var(--white);background:linear-gradient(135deg,#6f5a3c,#4e6a37 50%,#3a3a38)}
.play{position:absolute;left:202px;top:114px;width:54px;height:54px;border-radius:50%;background:rgba(255,255,255,.35)}

/* trainers */
.trainers{top:2024px;height:469px;background:linear-gradient(180deg,#17a0cc,#0e90c2 60%,#22a5d2)}
.trainers .section-title{top:64px;color:var(--white)}
.trainer-band{left:0;top:151px;width:1200px;height:228px;background:rgba(30,40,45,.45)}
.trainer-card{top:151px;width:250px;height:228px;overflow:hidden}
.trainer-card.intro{background:#2b2b2b;text-align:center;color:var(--white)}
.trainer-card.intro h3{margin-top:40px;font-size:20px;font-weight:400}
.trainer-card.intro p{margin:8px 26px 0;font-size:12px;line-height:18px;color:#d0d0d0}
.social-row{display:flex;justify-content:center;gap:8px;margin-top:16px}
.social-row span{width:26px;height:26px;border-radius:50%}
.trainer-photo{position:absolute;inset:0}
.trainer-name{position:absolute;left:0;bottom:12px;width:100%;text-align:center;font-size:20px;color:var(--white);text-shadow:0 1px 4px rgba(0,0,0,.6)}

/* philosophy */
.philosophy{top:2493px;height:316px;background:linear-gradient(135deg,#141414,#2a2a2a 50%,#121212)}
.philosophy p{left:196px;width:808px;top:78px;font-size:20px;line-height:33px;font-weight:600;color:var(--white);text-align:center}
.philosophy .btn{left:505px;top:187px;width:183px;height:43px;background:var(--brand);color:var(--white)}

/* contact */
.contact{top:2809px;height:458px;background:var(--white)}
.contact h2{top:66px;font-size:24px;font-weight:400;color:#222}
.contact .lead{top:116px;font-size:12px;color:var(--muted)}
.field{border-bottom:1px solid var(--line);font-size:12px;color:#9aa3a8;padding-bottom:8px}
.contact .btn{left:537px;top:345px;width:149px;height:45px;background:var(--brand);color:var(--white)}

/* footer */
.site-footer{top:3267px;height:116px;background:#0c0c0c}
.social-footer{left:462px;top:36px;display:flex;gap:18px}
.social-footer span{width:16px;height:16px;border-radius:50%;background:#cfcfcf}
.copyright{top:76px;font-size:11px;color:#777}
</style>
</head>
<body>

<header class="site-header">
  <div class="abs brand"><span class="brand-dot"></span><span class="brand-name">Summit</span></div>
  <div class="abs contact-chip" style="left:706px">
    <span class="ring"><svg width="18" height="18" viewBox="0 0 24 24"><path d="M6.6 10.8a15 15 0 0 0 6.6 6.6l2.2-2.2a1 1 0 0 1 1-.25 11 11 0 0 0 3.6.6 1 1 0 0 1 1 1V20a1 1 0 0 1-1 1A17 17 0 0 1 3 4a1 1 0 0 1 1-1h3.5a1 1 0 0 1 1 1 11 11 0 0 0 .6 3.6 1 1 0 0 1-.25 1z" fill="none" stroke="#0792cd" stroke-width="2"/></svg></span>
    <span>(555) - 010 2233</span>
  </div>
  <div class="abs contact-chip" style="left:898px">
    <span class="ring"><svg width="20" height="16" viewBox="0 0 20 16"><rect x="1" y="1" width="18" height="14" rx="2" fill="none" stroke="#0792cd" stroke-width="2"/><path d="M1 2l9 7 9-7" fill="none" stroke="#0792cd" stroke-width="2"/></svg></span>
    <span>info@Summit.com</span>
  </div>
</header>

<nav class="main-nav">
  <a href="#" style="left:135px">Home</a>
  <a href="#" style="left:225px">Class descriptions</a>
  <a href="#" style="left:393px">Gym description</a>
  <a href="#" style="left:552px">Class schedules</a>
  <a href="#" style="left:705px">Trainer profiles</a>
  <a href="#" style="left:857px">Gym philosophy</a>
  <a href="#" style="left:1018px">Contact</a>
</nav>

<section class="hero">
  <div class="hero-photo" role="img" aria-label="Athlete training on bars in a bright gym with wood and plants"></div>
  <h1 class="abs center hero-title">Summit is the UAE's first calisthenics<br>and parkour gym</h1>
  <div class="abs slider-arrow"><svg width="14" height="18" viewBox="0 0 14 18"><path d="M10 2L3 9l7 7" fill="none" stroke="#fff" stroke-width="2.5"/></svg></div>
</section>

<section class="welcome">
  <h2 class="abs center">WELCOME TO SUMMIT BODYFORM GYM</h2>
  <p class="abs">Sed ut perspiciatis unde omnis iste natus error sit voluptatem accusantium doloremque laudantium, totam rem aperiam, eaque ipsa quae ab illo inventore veritatis et quasi architecto beatae vitae dicta sunt explicabo. Nemo enim ipsam voluptatem quia voluptas sit aspernatur aut odit aut fugit, sed quia consequuntur magni dolores eos qui ratione voluptatem sequi nesciunt.</p>
  <a class="btn btn-outline-light" href="#">Learn More</a>
</section>

<section class="services">
  <h2 class="abs center section-title">OUR SERVICES</h2>
  <div class="abs service-card active" style="left:99px">
    <div class="service-icon"><svg width="44" height="24" viewBox="0 0 44 24"><rect x="2" y="6" width="6" height="12" rx="1" fill="#fff"/><rect x="9" y="2" width="6" height="20" rx="1" fill="#fff"/><rect x="15" y="10" width="14" height="4" fill="#fff"/><rect x="29" y="2" width="6" height="20" rx="1" fill="#fff"/><rect x="36" y="6" width="6" height="12" rx="1" fill="#fff"/></svg></div>
    <h3>Control Weight</h3>
    <p>Dolor sit amet, consectetur adipiscing elit, sed do eiusmod tempor incididunt ut labore et dolore magna aliqua.</p>
    <a class="btn" href="#">Read More</a>
  </div>
  <div class="abs service-card" style="left:354px">
    <div class="service-icon"><svg width="36" height="36" viewBox="0 0 36 36"><path d="M8 30c0-8 2-14 6-18l4-6h5l-2 7 3 3c5-1 8 3 8 7 0 4-3 7-8 7z" fill="#777"/></svg></div>
    <h3>Muscles Silhouette</h3>
    <p>Dolor sit amet, consectetur adipiscing elit, sed do eiusmod tempor incididunt ut labore et dolore magna aliqua.</p>
    <a class="btn" href="#">Read More</a>
  </div>
  <div class="abs service-card" style="left:609px">
    <div class="service-icon"><svg width="34" height="36" viewBox="0 0 34 36"><path d="M10 13a7 7 0 1 1 14 0" fill="none" stroke="#777" stroke-width="3"/><circle cx="17" cy="23" r="11" fill="#777"/><circle cx="17" cy="24" r="4" fill="none" stroke="#fff" stroke-width="1.5"/></svg></div>
    <h3>Circular Weight</h3>
    <p>Dolor sit amet, consectetur adipiscing elit, sed do eiusmod tempor incididunt ut labore et dolore magna aliqua.</p>
    <a class="btn" href="#">Read More</a>
  </div>
  <div class="abs service-card" style="left:862px">
    <div class="service-icon"><svg width="38" height="34" viewBox="0 0 38 34"><path d="M19 32L5 18A8 8 0 0 1 19 7a8 8 0 0 1 14 11z" fill="none" stroke="#777" stroke-width="2.5"/><path d="M3 17h9l3-5 4 9 3-4h13" fill="none" stroke="#777" stroke-width="2"/></svg></div>
    <h3>Control Of Heart Beats</h3>
    <p>Dolor sit amet, consectetur adipiscing elit, sed do eiusmod tempor incididunt ut labore et dolore magna aliqua.</p>
    <a class="btn" href="#">Read More</a>
  </div>
</section>

<section class="gym-description">
  <h2 class="abs">DESCRIPTION OF OUR GYM</h2>
  <p class="abs" style="top:120px">Sed ut perspiciatis unde omnis iste natus error sit voluptatem accusantium doloremque laudantium, totam rem aperiam, eaque ipsa quae ab illo inventore veritatis et quasi architecto beatae vitae dicta sunt explicabo. Nemo enim ipsam voluptatem quia voluptas sit aspernatur aut odit aut fugit, sed quia consequuntur magni dolores eos qui ratione voluptatem sequi nesciunt. Neque porro quisquam est.</p>
  <p class="abs" style="top:237px">Qeius modi tempora incidunt ut labore et dolore magnam aliquam quaerat voluptatem. Ut enim ad minima veniam, quis nostrum exercitationem ullam corporis suscipit laboriosam, nisi ut aliquid ex ea commodi consequatur.</p>
  <a class="btn" href="#">Read More</a>
  <div class="abs video-frame" role="img" aria-label="Gym video still: plant wall above a rack of dumbbells">
    <span class="play"></span>
  </div>
</section>

<section class="trainers">
  <h2 class="abs center section-title">TRAINER PROFILES</h2>
  <div class="trainer-band abs"></div>
  <div class="abs trainer-card intro" style="left:99px">
    <h3>Eiusmod Tempor</h3>
    <p>consectetur adipiscing elit, sed do eiusmod tempor incididunt ut labore et dolore magna aliqua. Ut enim ad minim veniam.</p>
    <div class="social-row"><span style="background:#3fa9e0"></span><span style="background:#e58a2c"></span><span style="background:#3b5ba0"></span></div>
  </div>
  <div class="abs trainer-card" style="left:350px">
    <div class="trainer-photo" role="img" aria-label="Trainer portrait doing a floor exercise" style="background:linear-gradient(135deg,#5a5a55,#8c8a80 50%,#3f3f3c)"></div>
    <div class="trainer-name">Occaecat Cupidatat</div>
  </div>
  <div class="abs trainer-card" style="left:600px">
    <div class="trainer-photo" role="img" aria-label="Trainer portrait with towel" style="background:linear-gradient(135deg,#d9d6cf,#b9b2a6 50%,#8f8a80)"></div>
    <div class="trainer-name">Voluptatem Accusa</div>
  </div>
  <div class="abs trainer-card" style="left:851px">
    <div class="trainer-photo" role="img" aria-label="Trainer portrait" style="background:linear-gradient(135deg,#cfc9c2,#a59486 50%,#6e5b4f)"></div>
    <div class="trainer-name">Neque porro</div>
  </div>
</section>

<section class="philosophy">
  <p class="abs">The theme under which the gym revolves is that one does not require any machinery to workout as our bodies could be themselves the machinery.</p>
  <a class="btn" href="#">Free First Trial Class</a>
</section>

<section class="contact">
  <h2 class="abs center">CONTACT US</h2>
  <div class="abs center lead">Lorem ipsum dolor sit amet, consectetur adipiscing elit.</div>
  <div class="abs field" style="left:124px;top:178px;width:447px">Name</div>
  <div class="abs field" style="left:124px;top:230px;width:447px">Email</div>
  <div class="abs field" style="left:124px;top:282px;width:954px">Subject</div>
  <div class="abs" style="left:638px;top:178px;font-size:12px;color:#9aa3a8">Message</div>
  <a class="btn" href="#">Send Message</a>
</section>

<footer class="site-footer">
  <div class="abs social-footer"><span></span><span></span><span></span><span></span><span></span><span></span><span></span></div>
  <div class="abs center copyright">Copyright@2015Summit.all Rights Reserved</div>
</footer>

</body>
</html>
```